Agriculture Technology Website Design Project

We need a new website for a company called Orchard Pulse Networks. We have a document laid out with all of the requirements (see below) and would like you to follow the instructions on there. In this document, there is all of the copy that must be included on the website and what order it should go in as well as images. These images have specific names and are listed in the document as to where they should go. Please make this one continuous site that users can easily scroll through. We would like it to be sleek and modern with as little clutter as possible. Please refer to the brochure that we have posted below (Meadow Analytica.pdf) for a design we have had done for the company in the past. We really like this design and it would be great if the color scheme was similar on the website.

Industry/Entity Type

Agriculture

Number of Pages Required

1 page

Font styles to use
Sans Serif

```html
<!DOCTYPE html>
<html lang="en">
<head>
<meta charset="utf-8">
<title>Orchard Pulse Networks</title>
<link href="https://fonts.googleapis.com/css2?family=Montserrat:wght@300;400;500;600;700&display=swap" rel="stylesheet">
<style>
:root{
  --green:#2a8a06;
  --green-dark:#1f7304;
  --green-mid:#8cc16b;
  --green-pale:#d6e9c8;
  --ink:#222;
  --muted:#666;
  --night:#1d2a1b;
  --white:#fff;
}
*{margin:0;padding:0;box-sizing:border-box}
html,body{width:1200px;height:5115px;overflow:hidden}
body{position:relative;font-family:'Montserrat',sans-serif;color:var(--ink);background:var(--white)}
.abs{position:absolute}
svg{display:block}
.btn{position:absolute;display:flex;align-items:center;justify-content:center;background:var(--green);color:var(--white);border-radius:28px;font-size:19px;font-weight:500;text-decoration:none}

/* hero */
.hero{left:0;top:0;width:1200px;height:700px;background:linear-gradient(180deg,#243424 0%,#2f4a2b 35%,#2d4a22 60%,#1c3014 100%)}
.brand{left:76px;top:30px;display:flex;align-items:center;gap:10px;color:var(--green);font-size:13px;font-weight:600}
.brand i{width:22px;height:22px;border-radius:50%;background:var(--green)}
.nav{right:74px;top:30px;display:flex;gap:22px;font-size:13.5px;color:var(--white);align-items:center}
.nav .home{width:100px;height:76px;margin-top:-46px;border-radius:0 0 50px 50px;background:var(--green-dark);display:flex;align-items:flex-end;justify-content:center;padding-bottom:12px;margin-right:-22px;margin-left:-20px}
.hero-title{left:0;width:1200px;top:245px;text-align:center;color:var(--white);font-size:48px;font-weight:700;letter-spacing:1px;line-height:58px}
.hero-title span{color:var(--green)}
.hero-tagline{left:0;width:1200px;top:308px;text-align:center;color:var(--white);font-size:18px}
.hero-wave{left:0;top:520px}

.seed-dot{left:588px;top:710px;width:24px;height:24px;border-radius:50%;background:var(--green)}

/* services */
.service{top:820px;width:210px;text-align:center}
.service .ring{width:96px;height:96px;margin:0 auto;border-radius:50%;background:var(--green);display:flex;align-items:center;justify-content:center}
.service .ring.featured{box-shadow:0 0 0 6px var(--white),0 0 0 8px var(--green)}
.service h3{margin-top:36px;font-size:15.5px;font-weight:500;line-height:26px;color:var(--ink)}
.service h3.active{color:var(--green)}
.service p{margin-top:18px;font-size:14px;line-height:25px;color:var(--muted)}

/* integrator */
.integrator-title{left:100px;top:1240px;font-size:38px;font-weight:600;line-height:46px;color:var(--green)}
.goal{left:102px;top:1350px;width:420px;font-size:17px;line-height:27px}
.copy{font-size:14px;line-height:27px;color:var(--muted)}
.photo{background:linear-gradient(135deg,#4a6b2a,#87a64b 60%,#cfd8b8)}
.deco-ring{border-radius:50%;border:40px solid var(--green-pale)}

/* why */
.why-title{left:680px;top:1893px;font-size:38px;font-weight:600;color:var(--green)}
.why-sub{left:682px;top:1950px;font-size:17px}

/* meadow */
.meadow-brand{left:0;width:1200px;top:2378px;display:flex;justify-content:center;align-items:center;gap:14px;color:var(--white)}
.meadow-brand i{width:44px;height:44px;border-radius:50%;background:var(--white)}
.meadow-brand span{font-size:40px;font-weight:300}
.meadow-title{left:0;width:1200px;top:2478px;text-align:center;color:var(--white);font-size:38px;font-weight:600}
.meadow-copy{left:250px;width:700px;top:2538px;text-align:center;color:var(--white);font-size:14px;line-height:27px}
.tool{top:2672px;width:240px;text-align:center}
.tool .disc{width:112px;height:112px;margin:0 auto;border-radius:50%;background:var(--white);box-shadow:0 4px 14px rgba(0,0,0,.18);display:flex;align-items:center;justify-content:center}
.tool .disc.solid{background:var(--green);box-shadow:0 0 0 5px var(--white),0 0 0 7px var(--green)}
.tool h4{margin-top:22px;font-size:15.5px;font-weight:500;line-height:24px}

.irrig-title{left:0;width:1200px;top:2915px;text-align:center;font-size:36px;font-weight:600;line-height:46px;color:var(--green)}
.arrow{width:56px;height:56px;border-radius:50%;border:2px solid var(--green);display:flex;align-items:center;justify-content:center}
.arrow.grey{border-color:#b8b8b8}

/* chemigation */
.chem-title{left:0;width:1200px;top:3745px;text-align:center;color:var(--white);font-size:27px;font-weight:500}
.chem-copy{left:200px;width:800px;top:3822px;text-align:center;color:var(--white);font-size:14px;line-height:27px}

/* partners */
.partners-title{left:0;width:1200px;top:4120px;text-align:center;font-size:38px;font-weight:600;color:var(--green)}
.partner-label{top:4222px;font-size:19px;font-weight:500;color:var(--green);letter-spacing:.5px}
.partner-box{top:4268px;width:504px;height:122px;background:var(--white);box-shadow:0 2px 10px rgba(0,0,0,.1);display:flex;align-items:center;justify-content:space-around;padding:0 14px}
.partner{display:flex;align-items:center;gap:8px;font-size:16px;font-weight:500;color:#3a4a5a}
.partner i{width:30px;height:30px;border-radius:50%;background:#6d7f92;flex:none}

/* footer */
.footer-bg{left:0;top:4600px;width:1200px;height:515px;background:linear-gradient(180deg,#243222,#1a2517 60%,#141d12)}
.footer-brand{left:0;width:1200px;top:4660px;display:flex;flex-direction:column;align-items:center;gap:10px;color:var(--green);font-size:30px;font-weight:700}
.footer-brand i{width:56px;height:56px;border-radius:50%;background:var(--green)}
.social{left:522px;top:4770px;display:flex;gap:13px}
.social i{width:44px;height:44px;border-radius:50%;background:var(--green)}
.contact-strip{left:210px;top:4840px;width:780px;height:100px;border:1px solid rgba(255,255,255,.35);display:flex;color:var(--white);font-size:13.5px;line-height:25px}
.contact-strip div{flex:1;display:flex;align-items:center;gap:16px;padding-left:22px;border-right:1px solid rgba(255,255,255,.35)}
.contact-strip div:last-child{border-right:none}
.foot-links{left:0;width:1200px;top:4983px;text-align:center;color:var(--white);font-size:13.5px;word-spacing:4px}
.copyright{left:0;width:1200px;top:5017px;text-align:center;color:var(--white);font-size:13.5px}
</style>
</head>
<body>

<!-- hero -->
<section class="abs hero" role="img" aria-label="Sprinklers irrigating an orchard at dusk"></section>
<div class="abs brand"><i></i>ORCHARD PULSE NETWORKS</div>
<nav class="abs nav"><span class="home">HOME</span><span>ABOUT US</span><span>WHY OPN ?</span><span>PRODUCTS</span><span>PARTNERS</span><span>CONTACT US</span></nav>
<h1 class="abs hero-title">ORCHARD <span>PULSE</span> NETWORKS</h1>
<p class="abs hero-tagline">Bringing industrial automation to the farm</p>
<a class="btn" style="left:508px;top:352px;width:184px;height:54px">CONTACT US</a>
<svg class="abs hero-wave" width="1200" height="181" viewBox="0 0 1200 181">
  <path d="M0,120 C400,60 800,20 1200,0 L1200,181 L0,181Z" fill="#8cc16b"/>
  <path d="M0,150 C400,95 800,70 1200,70 L1200,181 L0,181Z" fill="#c9e2b5"/>
  <path d="M0,181 C450,120 850,100 1200,110 L1200,181Z" fill="#fff"/>
</svg>
<div class="abs seed-dot"></div>

<!-- services -->
<div class="abs service" style="left:71px">
  <div class="ring featured"><svg width="48" height="48" viewBox="0 0 48 48" fill="none" stroke="#fff" stroke-width="2"><rect x="8" y="18" width="20" height="20" rx="2"/><rect x="30" y="24" width="10" height="14"/><path d="M18 18V10h6M4 40h40"/></svg></div>
  <h3 class="active">CHEMIGATION<br>AUTOMATION</h3>
  <p>Control of your fertilizer injection and monitor tank levels to optimize inputs.</p>
</div>
<div class="abs service" style="left:285px">
  <div class="ring"><svg width="44" height="44" viewBox="0 0 44 44" fill="none" stroke="#fff" stroke-width="2"><rect x="6" y="6" width="32" height="32"/><path d="M10 32l8-8 6 5 10-12M28 17h6v6"/></svg></div>
  <h3>CROP<br>MONITORING</h3>
  <p>Ensuring that you have real-time information to optimize irrigation management</p>
</div>
<div class="abs service" style="left:495px">
  <div class="ring"><svg width="46" height="46" viewBox="0 0 46 46" fill="none" stroke="#fff" stroke-width="2"><rect x="4" y="8" width="38" height="30" rx="2"/><path d="M4 15h38"/><circle cx="18" cy="28" r="5"/><circle cx="30" cy="30" r="3"/></svg></div>
  <h3>PUMP MONITORING<br>&amp; CONTROL</h3>
  <p>Scalable and cost-effective pump monitoring with built-in remote control</p>
</div>
<div class="abs service" style="left:709px">
  <div class="ring"><svg width="44" height="44" viewBox="0 0 44 44" fill="none" stroke="#fff" stroke-width="2"><rect x="7" y="5" width="30" height="34" rx="2"/><path d="M7 12h30"/><circle cx="22" cy="26" r="8"/><path d="M14 26h16"/></svg></div>
  <h3>IRRIGATION<br>AUTOMATION</h3>
  <p>Upgrade your irrigation system: from retrofit to ranch-wide automation</p>
</div>
<div class="abs service" style="left:919px">
  <div class="ring"><svg width="44" height="44" viewBox="0 0 44 44" fill="none" stroke="#fff" stroke-width="2.2"><path d="M12 8l6 8-4 4c2 5 5 8 10 10l4-4 8 6-4 6C20 38 6 24 6 12z"/><path d="M26 8a10 10 0 0 1 10 10M26 14a4 4 0 0 1 4 4"/></svg></div>
  <h3 style="margin-top:36px;line-height:52px">CONTACT US</h3>
  <p style="margin-top:0">For immediate support call (555 014 - 2290)</p>
</div>

<!-- integrator -->
<h2 class="abs integrator-title">OPN IS SYSTEMS<br>INTEGRATOR</h2>
<p class="abs goal">OUR GOAL: To Be your Trusted Partner for Technology Adoption</p>
<p class="abs copy" style="left:102px;top:1414px;width:440px">Our focus is on helping California growers design, build and adopt effective irrigation management solutions.Our team has worked together for over 15 years, providing monitoring and control systems for 60+ crops that have successfully helped</p>
<p class="abs copy" style="left:102px;top:1570px;width:440px">Over 500 farms significantly improve irrigation management. We also farm our own 200 acre technology lab to help ensure we deliver reliable monitoring &amp; automation to your farm.</p>
<a class="btn" style="left:100px;top:1695px;width:164px;height:48px">PRODUCTS</a>
<div class="abs deco-ring" style="left:860px;top:1275px;width:262px;height:262px"></div>
<div class="abs photo" style="left:638px;top:1244px;width:286px;height:306px;background:linear-gradient(135deg,#2f4a24,#5d7a3a 55%,#c9b7a0)" role="img" aria-label="Almonds ripening on a branch"></div>
<div class="abs photo" style="left:786px;top:1420px;width:286px;height:318px;background:linear-gradient(180deg,#d9dde2 0%,#a9bf3e 30%,#6f8f22 75%,#8a7a5e)" role="img" aria-label="Young almond tree in an orchard"></div>

<!-- why -->
<div class="abs deco-ring" style="left:-70px;top:1950px;width:270px;height:270px"></div>
<div class="abs photo" style="left:126px;top:1880px;width:444px;height:334px;background:linear-gradient(180deg,#cfe0ef 0%,#b9a78a 30%,#5f7a2e 55%,#3f5a1f 100%)" role="img" aria-label="Vineyard rows beneath dry hills"></div>
<h2 class="abs why-title">WHY OPN?</h2>
<p class="abs why-sub">We're Your Local Orchard Pulse Team.</p>
<p class="abs copy" style="left:682px;top:1995px;width:400px">We are experts at deploying Information Technology for irrigation management. We partner with our customers to deliver the right solutions. Everything we sell is off-the-shelf, cost-effective and reliable</p>
<a class="btn" style="left:680px;top:2147px;width:198px;height:52px">GET IN TOUCH</a>

<!-- meadow analytica -->
<svg class="abs" style="left:0;top:2240px" width="1200" height="570" viewBox="0 0 1200 570">
  <path d="M0,62 C400,62 800,40 1200,8 L1200,570 C900,480 400,430 0,440Z" fill="#2a8a06"/>
</svg>
<div class="abs meadow-brand"><i></i><span>Meadow Analytica</span></div>
<h2 class="abs meadow-title">MEADOW ANALYTICA</h2>
<p class="abs meadow-copy">Meadow Analytica is a cost-effective suite of tools built by Orchard Pulse Networks for irrigation management, providing farmers access to state-of-the-art industrial monitoring and control tools already widely adopted in other industries</p>
<div class="abs tool" style="left:254px">
  <div class="disc"><svg width="50" height="50" viewBox="0 0 44 44" fill="none" stroke="#2a8a06" stroke-width="2"><rect x="6" y="6" width="32" height="32"/><path d="M10 32l8-8 6 5 10-12M28 17h6v6"/></svg></div>
  <h4>REMOTE CROP<br>MONITORING</h4>
</div>
<div class="abs tool" style="left:480px;top:2676px">
  <div class="disc"><svg width="52" height="52" viewBox="0 0 46 46" fill="none" stroke="#2a8a06" stroke-width="2"><rect x="4" y="8" width="38" height="30" rx="2"/><path d="M4 15h38"/><circle cx="18" cy="28" r="5"/><circle cx="30" cy="30" r="3"/></svg></div>
  <h4>REMOTE PUMP<br>MONITORING &amp; CONTROL</h4>
</div>
<div class="abs tool" style="left:732px">
  <div class="disc solid"><svg width="50" height="50" viewBox="0 0 44 44" fill="none" stroke="#fff" stroke-width="2"><rect x="7" y="5" width="30" height="34" rx="2"/><path d="M7 12h30"/><circle cx="22" cy="26" r="8"/><path d="M14 26h16"/></svg></div>
  <h4>IRRIGATION<br>AUTOMATION</h4>
</div>

<h2 class="abs irrig-title">WHAT IS IRRIGATION<br>AUTOMATION?</h2>
<div class="abs arrow grey" style="left:202px;top:3182px"><svg width="14" height="22" viewBox="0 0 14 22" fill="none" stroke="#b8b8b8" stroke-width="2"><path d="M12 2L3 11l9 9"/></svg></div>
<div class="abs photo" style="left:300px;top:3030px;width:596px;height:354px;background:linear-gradient(180deg,#b7cfe2 0%,#7f9a5a 35%,#c8c4b8 55%,#a58a68 100%)" role="img" aria-label="Filter station and pump equipment in an orchard"></div>
<div class="abs arrow" style="left:932px;top:3182px"><svg width="14" height="22" viewBox="0 0 14 22" fill="none" stroke="#2a8a06" stroke-width="2"><path d="M2 2l9 9-9 9"/></svg></div>
<p class="abs copy" style="left:290px;top:3408px;width:620px;text-align:center">Meadow Analytica Irrigation Automation includes both valve and pump control systems that brings best-in-class industrial control technology to agriculture to provide farmers with cost-effective, easy-to-use solutions. Meadow Analytica provides the flexibility and remote control to support precise delivery of plant-water needs with a significant reduction in irrigation labor requirements, making it the most powerful solution in the industry.</p>
<div class="abs deco-ring" style="left:1045px;top:3460px;width:260px;height:260px"></div>

<!-- chemigation -->
<svg class="abs" style="left:0;top:3640px" width="1200" height="480" viewBox="0 0 1200 480">
  <path d="M0,140 C300,40 700,0 1200,12 L1200,420 C800,460 400,470 0,465Z" fill="#2a8a06"/>
</svg>
<h2 class="abs chem-title">CHEMIGATION AUTOMATION</h2>
<p class="abs chem-copy">Full scale fertilizer chemical injection system that automates fertigation and chemigation at critical times in your irrigation strategy. The system is set up to fertilize when your crop needs it the most. Along with pump and valve automation from your bulk tanks the system can monitor tank levels and record precise fertilizer delivery for each irrigation event and send critical alerts when tanks run low on material. Meadow Analytica supports an unlimited number of variations of product and blending options depending on how you want to blend different products.</p>

<!-- partners -->
<h2 class="abs partners-title">PARTNERS</h2>
<p class="abs partner-label" style="left:80px">SOFTWARE</p>
<p class="abs partner-label" style="left:620px">SOIL MOISTURE SENSORS</p>
<svg class="abs" style="left:34px;top:4316px" width="14" height="26" viewBox="0 0 14 26" fill="none" stroke="#aaa" stroke-width="2"><path d="M12 2L2 13l10 11"/></svg>
<div class="abs partner-box" style="left:78px">
  <span class="partner"><i></i>Gridline Controls</span>
  <span class="partner"><i></i>Tallyfield</span>
  <span class="partner">Rootcast Planner</span>
</div>
<div class="abs partner-box" style="left:620px">
  <span class="partner"><i style="background:#2a7fc1"></i>Loamwise</span>
  <span class="partner">Hexaterra Labs</span>
  <span class="partner"><i style="background:#2a7fc1"></i>Subsoil Metrics</span>
</div>
<svg class="abs" style="left:1152px;top:4316px" width="14" height="26" viewBox="0 0 14 26" fill="none" stroke="#aaa" stroke-width="2"><path d="M2 2l10 11L2 24"/></svg>

<!-- footer -->
<div class="abs footer-bg" role="img" aria-label="Orchard landscape at night"></div>
<svg class="abs" style="left:0;top:4420px" width="1200" height="200" viewBox="0 0 1200 200">
  <path d="M0,20 C500,30 900,80 1200,100 L1200,200 L0,200Z" fill="#cfe5bf"/>
  <path d="M0,80 C500,92 900,130 1200,145 L1200,200 L0,200Z" fill="#8cc16b"/>
  <path d="M0,145 C500,148 900,170 1200,185 L1200,200 L0,200Z" fill="#243222"/>
</svg>
<div class="abs footer-brand"><i></i>OPN</div>
<div class="abs social" aria-label="Social links"><i></i><i></i><i></i></div>
<div class="abs contact-strip">
  <div><svg width="20" height="28" viewBox="0 0 20 28"><path d="M10 0a10 10 0 0 0-10 10c0 8 10 18 10 18s10-10 10-18A10 10 0 0 0 10 0z" fill="#2a8a06"/><circle cx="10" cy="10" r="4" fill="#1d2a1b"/></svg><span>Lorem ipsum simple<br>text print text.</span></div>
  <div><svg width="24" height="24" viewBox="0 0 44 44"><path d="M12 6l7 9-4 5c2 5 5 8 10 10l5-4 9 7-5 7C20 40 4 24 4 11z" fill="#2a8a06"/></svg><span>Phone :<br>555 014 - 2290</span></div>
  <div><svg width="26" height="20" viewBox="0 0 26 20"><rect width="26" height="20" rx="2" fill="#2a8a06"/><path d="M2 3l11 8 11-8" stroke="#1d2a1b" stroke-width="2" fill="none"/></svg><span>Email :<br>hello@orchardpulse.example</span></div>
</div>
<p class="abs foot-links">Home | About | Why OPN? | Products | Partners | Contact</p>
<p class="abs copyright">©OPN - 2020 All rights reserved.</p>

</body>
</html>
```